Wren Hollow Farm Postcard Design

I am looking for a new postcard design to mail out this season. We are a Farm business that does wholesale and retail and bulk seasoned firewood sales. we sell firewood from anything from bagged wood to tractor trailer loads of wood. We sell firewood in bulk bags. Pick up or delivery available there is no order to big or too small. I need my business name and phone number on the cards Wren Hollow Farm 615-302-4187 (call or text) I would like it to say we are the best priced guaranteed. I want something that is simple and straight forward but also really catches the eye when they see these in the mail box. I attached my logo and feel free to use photos of split firewood if you would like. id like my email on the card Wrenhollowfarm47@maplepost.net.

Target Market(s)

Firewood purchasers

Industry/Entity Type

agriculture

Requirements
Must have
• email phone number logo

```html
<!DOCTYPE html>
<html lang="en">
<head>
<meta charset="UTF-8">
<title>Wren Hollow Farm – Bulk Firewood Postcard</title>
<link rel="stylesheet" href="https://fonts.googleapis.com/css2?family=Alegreya+Sans:wght@500;700;800;900&display=swap">
<style>
  :root {
    --wood-dark: #140b05;
    --wood-mid: #3a2412;
    --wood-warm: #5a3a1f;
    --tan-light: #f4dcb6;
    --tan-mid: #c79d6a;
    --tan-deep: #8c6437;
    --gold: #f6b21c;
    --cream: #fbe6cc;
    --white: #ffffff;
    --ink: #2a1a0e;
    --green: #1f7a3b;
    --green-edge: #f0d9a8;
    --pine: #1e6b34;
    --orange-top: #f9c21a;
    --orange-bottom: #ee5b1d;
    --beam: #6f6a62;
    --log-light: #d9a873;
    --log-dark: #7a5230;
  }
  * { margin: 0; padding: 0; box-sizing: border-box; }
  html, body { width: 1200px; height: 800px; overflow: hidden; background: #000; }
  body { font-family: "Alegreya Sans", sans-serif; }

  .postcard { position: relative; width: 1200px; height: 800px; overflow: hidden; }

  .plank-backdrop {
    position: absolute; inset: 0;
    background:
      linear-gradient(180deg, rgba(0,0,0,0.92) 0%, rgba(0,0,0,0.55) 30%, rgba(0,0,0,0.15) 65%, rgba(0,0,0,0.05) 100%),
      linear-gradient(90deg, var(--wood-dark), var(--wood-warm) 30%, var(--wood-mid) 55%, var(--wood-warm) 80%, var(--wood-dark));
  }

  .woodpile {
    position: absolute; left: 0; right: 0; top: 605px; bottom: 0;
    background: linear-gradient(180deg, var(--log-light) 0%, #c08f5c 45%, var(--log-dark) 100%);
  }
  .woodpile-beam {
    position: absolute; left: 0; right: 0; top: 612px; height: 28px;
    background: linear-gradient(180deg, #8a857c, var(--beam) 60%, #4a463f);
  }

  .pine { position: absolute; top: 50px; width: 60px; height: 86px; }
  .pine--left { left: 60px; }
  .pine--right { left: 1090px; }

  .badge-best {
    position: absolute; left: 60px; top: 195px; width: 150px; height: 84px;
    background: var(--green); border: 2px solid var(--green-edge); border-radius: 20px;
    color: var(--white); font-weight: 800; font-size: 22px; line-height: 23px;
    padding: 17px 0 0 10px;
  }
  .shield { position: absolute; left: 70px; top: 156px; width: 40px; height: 46px; }

  .truck { position: absolute; left: 1018px; top: 142px; width: 76px; height: 40px; }
  .badge-delivery {
    position: absolute; left: 1002px; top: 183px; width: 150px; height: 103px;
    background: linear-gradient(180deg, var(--orange-top), var(--orange-bottom));
    border: 2px solid var(--cream); border-radius: 22px 0 22px 22px;
    color: var(--white); font-weight: 800; font-size: 22px; line-height: 23px;
    padding: 18px 0 0 20px;
  }
  .badge-delivery .lead { color: #fff6c4; }

  .farm-name {
    position: absolute; left: 0; right: 0; top: 140px;
    text-align: center; font-weight: 800; font-size: 88px; line-height: 1;
    color: var(--gold);
  }

  .headline {
    position: absolute; left: 0; right: 0; top: 335px;
    text-align: center; font-weight: 900; font-size: 124px; line-height: 1; letter-spacing: -2px;
    background: linear-gradient(180deg, var(--tan-light) 0%, var(--tan-mid) 55%, var(--tan-deep) 100%);
    -webkit-background-clip: text; background-clip: text; color: transparent;
    filter: drop-shadow(0 3px 2px rgba(0,0,0,0.6));
  }

  .phone-line {
    position: absolute; left: 0; right: 0; top: 458px;
    text-align: center; white-space: nowrap;
  }
  .phone-number { color: var(--white); font-weight: 800; font-size: 68px; }
  .phone-note { color: var(--cream); font-weight: 700; font-size: 46px; margin-left: 18px; }

  .email-pill {
    position: absolute; left: 340px; top: 544px; width: 520px; height: 42px;
    background: var(--cream); border-radius: 21px;
    display: flex; align-items: center; justify-content: center; gap: 10px;
    color: var(--ink); font-weight: 800; font-size: 27px;
  }
  .email-pill svg { width: 28px; height: 20px; }
</style>
</head>
<body>
<main class="postcard">
  <div class="plank-backdrop" role="img" aria-label="Dark weathered wooden barn plank wall"></div>
  <div class="woodpile" role="img" aria-label="Stacked split firewood pile"></div>
  <div class="woodpile-beam"></div>

  <svg class="pine pine--left" viewBox="0 0 60 86" role="img" aria-label="Pine tree icon">
    <polygon points="30,0 50,30 42,30 56,54 44,54 60,74 0,74 16,54 4,54 18,30 10,30" fill="var(--pine)"/>
    <rect x="27" y="74" width="6" height="12" fill="var(--pine)"/>
  </svg>
  <svg class="pine pine--right" viewBox="0 0 60 86" role="img" aria-label="Pine tree icon">
    <polygon points="30,0 50,30 42,30 56,54 44,54 60,74 0,74 16,54 4,54 18,30 10,30" fill="var(--pine)"/>
    <rect x="27" y="74" width="6" height="12" fill="var(--pine)"/>
  </svg>

  <svg class="shield" viewBox="0 0 40 46" aria-hidden="true">
    <path d="M20 2 L37 8 V22 C37 33 29 41 20 44 C11 41 3 33 3 22 V8 Z" fill="#e9cf9b"/>
    <path d="M12 23 L18 29 L29 16" fill="none" stroke="var(--ink)" stroke-width="3.5" stroke-linecap="round" stroke-linejoin="round"/>
  </svg>
  <div class="badge-best">Best Prices<br>Guaranteed</div>

  <svg class="truck" viewBox="0 0 76 40" role="img" aria-label="Pickup truck icon">
    <path d="M2 16 H40 V4 H56 L66 16 H74 V30 H2 Z" fill="#f28a1e"/>
    <rect x="44" y="8" width="10" height="8" fill="#fde7c2"/>
    <circle cx="16" cy="31" r="7" fill="#f28a1e" stroke="#fde7c2" stroke-width="3"/>
    <circle cx="60" cy="31" r="7" fill="#f28a1e" stroke="#fde7c2" stroke-width="3"/>
  </svg>
  <div class="badge-delivery"><span class="lead">Pick-up</span><br>or Delivery<br>Available</div>

  <h1 class="farm-name">Wren Hollow Farm</h1>

  <h2 class="headline">Bulk Firewood</h2>

  <p class="phone-line"><span class="phone-number">615-302-4187</span><span class="phone-note">(Call or Text)</span></p>

  <p class="email-pill">
    <svg viewBox="0 0 28 20" aria-hidden="true">
      <rect x="1" y="1" width="26" height="18" fill="var(--ink)"/>
      <path d="M1 1 L14 11 L27 1 M1 19 L11 9 M27 19 L17 9" fill="none" stroke="var(--cream)" stroke-width="2"/>
    </svg>
    Wrenhollowfarm47@maplepost.net
  </p>
</main>
</body>
</html>
```